QVR business card

Need a business card for a company that provides instructional design and elearning development services. The website is here: http://quorvane.studio/

I'm attaching a current logo, as well as the old business card design. While I like to keep it clean, the old design is too simplistic for my liking. The only idea I want to reuse from the old design is placing industry jargon on the back of the card, just need a better way to present it. But if you have other ideas for the back--feel free to experiment.

Please use the colors complementary to the color we have on the website. Thank you!

```html
<!DOCTYPE html>
<html lang="en">
<head>
<meta charset="utf-8">
<title>QVR business card</title>
<link rel="stylesheet" href="https://fonts.googleapis.com/css2?family=Open+Sans:wght@400;600;700&display=swap">
<style>
  :root {
    --backdrop: #3a3532;
    --card: #050505;
    --card-glow: #1d1d1f;
    --teal: #2bb8ad;
    --teal-light: #5fd0c0;
    --cream: #f1e9b0;
    --white: #f4f4f4;
    --muted: #8a8a8a;
  }
  * { margin: 0; padding: 0; box-sizing: border-box; }
  html, body { width: 1200px; height: 844px; overflow: hidden; }
  body {
    background: var(--backdrop);
    font-family: "Open Sans", Arial, sans-serif;
    position: relative;
  }
  .card {
    position: absolute;
    top: 267px;
    width: 540px;
    height: 310px;
    background: var(--card);
    overflow: hidden;
    box-shadow: 0 10px 30px rgba(0,0,0,.45);
  }
  .card--contact { left: 40px; }
  .card--services {
    left: 620px;
    background: radial-gradient(ellipse at 50% 30%, var(--card-glow) 0%, var(--card) 70%);
  }

  /* contact side */
  .edge-band {
    position: absolute;
    left: 0; right: 0;
    height: 14px;
  }
  .edge-band--top {
    top: 18px;
    background: linear-gradient(to bottom, var(--teal) 0 60%, var(--cream) 60% 100%);
  }
  .edge-band--bottom {
    bottom: 18px;
    background: linear-gradient(to bottom, var(--cream) 0 40%, var(--teal) 40% 100%);
  }
  .contact {
    position: absolute;
    left: 0; right: 0;
    top: 108px;
    text-align: center;
    color: var(--white);
  }
  .contact__name {
    font-weight: 600;
    font-size: 17px;
    color: var(--teal-light);
    margin-bottom: 26px;
  }
  .contact__line {
    font-size: 14px;
    line-height: 19px;
  }

  /* services side */
  .edge-tab {
    position: absolute;
    width: 14px;
    height: 40px;
    background: linear-gradient(to bottom, var(--teal) 0%, var(--cream) 100%);
  }
  .edge-tab--right { right: 0; top: 34px; }
  .edge-tab--left { left: 0; top: 196px; }
  .brand {
    position: absolute;
    top: 44px;
    left: 0; right: 0;
    display: flex;
    justify-content: center;
    align-items: center;
    gap: 12px;
  }
  .brand__mark {
    width: 30px; height: 30px;
    background: var(--teal);
  }
  .brand__name {
    font-weight: 700;
    font-size: 40px;
    line-height: 1;
    color: var(--teal);
    letter-spacing: 1px;
  }
  .services__heading {
    position: absolute;
    top: 120px;
    left: 0; right: 0;
    text-align: center;
    font-weight: 600;
    font-size: 15px;
    color: var(--teal-light);
    letter-spacing: .5px;
  }
  .services__list {
    position: absolute;
    top: 158px;
    left: 0; right: 0;
    display: grid;
    grid-template-columns: 1fr 20px 1fr;
    row-gap: 12px;
    align-items: center;
    font-size: 13px;
    font-weight: 600;
    color: var(--white);
  }
  .services__item--left { text-align: right; }
  .services__item--right { text-align: left; }
  .services__dot {
    width: 6px; height: 6px;
    border-radius: 50%;
    background: var(--teal);
    justify-self: center;
  }
</style>
</head>
<body>
  <section class="card card--contact">
    <div class="edge-band edge-band--top"></div>
    <div class="contact">
      <p class="contact__name">Marek Halvorsen</p>
      <p class="contact__line">Phone: 555-014-2287</p>
      <p class="contact__line">Email: mhalvorsen@quorvane.studio</p>
      <p class="contact__line">Website: www.quorvane.studio</p>
    </div>
    <div class="edge-band edge-band--bottom"></div>
  </section>

  <section class="card card--services">
    <div class="edge-tab edge-tab--right"></div>
    <div class="edge-tab edge-tab--left"></div>
    <div class="brand">
      <span class="brand__mark"></span>
      <span class="brand__name">QVR</span>
    </div>
    <h2 class="services__heading">HOW CAN WE HELP?</h2>
    <div class="services__list">
      <span class="services__item services__item--left">Mobile Learning Scorm</span>
      <span class="services__dot"></span>
      <span class="services__item services__item--right">Instructional Design Lms</span>
      <span class="services__item services__item--left">Moocs Elearning Html5</span>
      <span class="services__dot"></span>
      <span class="services__item services__item--right">Adult Learning Theory</span>
      <span class="services__item services__item--left">Gamification Classroom</span>
      <span class="services__dot"></span>
      <span class="services__item services__item--right">Xapi Blended Learning</span>
    </div>
  </section>
</body>
</html>
```